creation of a business card design for a company specializing in the creation...

I would like to create a design for a professional business card on a black background and with the company's colors (I am attaching some files: including the logo in horizontal and centered format, I am also attaching a recent project design a T-shirt, this is the one I chose to give you an idea of my preferences.

we are in the process of developing a new website design, it is still in the development phase but it can be viewed at the following address: www.vantrelmo.be to give you other ideas about the company
you will see for yourself the subject of my main activity: company specializing in the construction of stairs

I would like a business card that stands out from the rest with a unique design

here is the informations
Name: Lucien Barthel
Function: Manager
Address: Rue Moulinet du Parc 42
7180 Fontelle
telephone: +32 468 219 804
email: info@rx7p.be
website: rx7p. be
social networks: Facebook, YouTube, TikTok, Instagram

Target Market(s)

customer who wants to have a beautiful staircase built

Industry/Entity Type

contruction d'escalier

Contact Information for Business Card

Adresse. Numero de telephone, site web, le texte : "Createur d'escalier", logo recto-verso, icone des reseaux sociaux

Requirements
Must have
• the mention: Stair creator
Nice to have
• an illustration of a designer staircase
Should not have
• do not distort the logo

```html
<!DOCTYPE html>
<html lang="fr">
<head>
<meta charset="utf-8">
<title>RX7P – Carte de visite</title>
<link rel="stylesheet" href="https://fonts.googleapis.com/css2?family=Montserrat:wght@400;500;600;700&display=swap">
<style>
  :root {
    --page: #1c1c1e;
    --card: #0f0f10;
    --card-back: #111112;
    --blue: #6694b3;
    --blue-light: #9cc0d8;
    --white: #ffffff;
    --silver: #c9ccd0;
    --rule: #d8d8d8;
  }
  * { box-sizing: border-box; margin: 0; padding: 0; }
  html, body { width: 1200px; height: 800px; overflow: hidden; }
  body {
    background: var(--page);
    font-family: "Montserrat", Arial, sans-serif;
    color: var(--white);
    position: relative;
  }
  .card {
    position: absolute;
    top: 225px;
    width: 540px;
    height: 350px;
    border-radius: 18px;
    overflow: hidden;
    box-shadow: 0 20px 40px rgba(0,0,0,.55);
  }
  .card--front { left: 40px; background: var(--card); }
  .card--back { left: 620px; background: var(--card-back); }

  .brand {
    position: absolute; top: 40px; right: 36px;
    display: flex; align-items: center; gap: 12px;
  }
  .brand__mark { width: 34px; height: 34px; background: var(--blue); }
  .brand__name {
    font-weight: 700; font-size: 38px; letter-spacing: 4px;
    color: var(--white); line-height: 1;
  }
  .rule { position: absolute; height: 1px; background: var(--rule); }
  .rule--top { left: 190px; right: 36px; top: 130px; }
  .rule--person { left: 36px; width: 220px; top: 222px; }
  .address {
    position: absolute; right: 36px; top: 146px; text-align: right;
    font-size: 14px; font-weight: 500; line-height: 1.35; font-style: normal;
  }
  .person { position: absolute; left: 36px; top: 158px; }
  .person__name {
    font-size: 29px; font-weight: 700; color: var(--blue); line-height: 1;
  }
  .person__role {
    font-size: 14px; font-weight: 500; letter-spacing: 1px; margin-top: 6px;
  }
  .contacts {
    position: absolute; left: 36px; top: 232px; list-style: none;
    font-size: 14px; font-weight: 500; line-height: 1;
  }
  .contacts li { display: flex; align-items: center; gap: 10px; height: 22px; }
  .contacts svg { width: 15px; height: 15px; flex: none; }
  .band { position: absolute; left: 0; bottom: 0; width: 540px; height: 60px; }
  .social {
    position: absolute; right: 40px; bottom: 30px;
    display: flex; align-items: center; gap: 6px;
    font-size: 11px; font-weight: 600; color: var(--white);
  }
  .social__dot { width: 12px; height: 12px; border-radius: 50%; background: var(--white); }

  .back-brand {
    position: absolute; left: 50%; top: 50%;
    transform: translate(-50%, -50%);
    display: flex; align-items: center; gap: 18px;
  }
  .back-brand__mark {
    width: 70px; height: 70px;
    background: linear-gradient(135deg, #2a2a2c, #050505);
  }
  .back-brand__name {
    font-weight: 700; font-size: 72px; letter-spacing: 8px;
    color: var(--silver); line-height: 1;
  }
</style>
</head>
<body>

<section class="card card--front" aria-label="Recto">
  <div class="brand">
    <span class="brand__mark"></span>
    <div class="brand__name">RX7P</div>
  </div>

  <div class="rule rule--top"></div>

  <address class="address">
    Rue Moulinet du Parc 42<br>7180 Fontelle
  </address>

  <div class="person">
    <h1 class="person__name">Lucien Barthel</h1>
    <p class="person__role">MANAGER</p>
  </div>

  <div class="rule rule--person"></div>

  <ul class="contacts">
    <li>
      <svg viewBox="0 0 24 24" fill="none" stroke="#6694b3" stroke-width="2.4" stroke-linecap="round"><path d="M5 4h4l2 5-2.5 1.5a11 11 0 0 0 5 5L15 13l5 2v4a2 2 0 0 1-2 2A16 16 0 0 1 3 6a2 2 0 0 1 2-2z"/></svg>
      +99 468 219 804
    </li>
    <li>
      <svg viewBox="0 0 24 24" fill="none" stroke="#6694b3" stroke-width="2.4" stroke-linejoin="round"><rect x="3" y="5" width="18" height="14"/><path d="M3 5l9 8 9-8"/></svg>
      info@rx7p.be
    </li>
    <li>
      <svg viewBox="0 0 24 24" fill="none" stroke="#6694b3" stroke-width="2.2"><circle cx="12" cy="12" r="9"/><path d="M3 12h18M12 3c3 3 3 15 0 18M12 3c-3 3-3 15 0 18"/></svg>
      www.rx7p. be
    </li>
  </ul>

  <svg class="band" viewBox="0 0 540 60" preserveAspectRatio="none" aria-hidden="true">
    <polygon points="0,44 320,44 340,38 540,38 540,60 0,60" fill="#9cc0d8"/>
    <polygon points="0,50 330,50 350,8 540,8 540,60 0,60" fill="#6694b3"/>
  </svg>

  <div class="social">
    <span class="social__dot"></span>
    <span class="social__handle">@rx7p</span>
  </div>
</section>

<section class="card card--back" aria-label="Verso">
  <div class="back-brand">
    <span class="back-brand__mark"></span>
    <div class="back-brand__name">RX7P</div>
  </div>
</section>

</body>
</html>
```